Business Card for a mobile physiotherapy company

I need a layout for a business card for a mobile physiotherapy company.
Slogan is "Mobile Physiotherapy - Your Road To Recovery"
Phone number is 867-555-0142
Email VardenTherapy@postnest.ca (subject to change with website)
Website www.VardenTherapy.ca
My name and credentials: Luke Varden Luke Varden, BSc(kin), MPT, CAFCI, IMS
Information maybe included: Direct Billing, Services including Physiotherapy, IMS, acupuncture
Maybe include facebook and instagram logos
One side with the logo clean and sharp
Other side with details, try not to look too busy, keep everything concise

```html
<!DOCTYPE html>
<html lang="en">
<head>
<meta charset="utf-8">
<title>Varden Therapy – Business Card</title>
<link href="https://fonts.googleapis.com/css2?family=Roboto:wght@400;500;700&display=swap" rel="stylesheet">
<style>
  :root {
    --bg: #dedede;
    --teal: #16594f;
    --teal-mid: #2d6675;
    --navy: #2b5079;
    --blue: #3e5f92;
    --green: #176152;
    --ink: #333a40;
    --white: #ffffff;
  }
  * { margin: 0; padding: 0; box-sizing: border-box; }
  html, body { width: 1200px; height: 900px; overflow: hidden; }
  body {
    background: var(--bg);
    font-family: "Roboto", Arial, sans-serif;
    display: flex; flex-direction: column; align-items: center; justify-content: center;
    gap: 40px;
  }
  .card {
    width: 700px; height: 400px; position: relative;
    box-shadow: 0 6px 18px rgba(0,0,0,0.15);
  }
  /* Front */
  .card-front {
    background: linear-gradient(135deg, var(--teal) 0%, var(--teal-mid) 50%, var(--navy) 100%);
    color: var(--white);
  }
  .brand-front {
    position: absolute; top: 120px; left: 0; right: 0;
    display: flex; align-items: center; justify-content: center; gap: 16px;
  }
  .brand-mark { width: 34px; height: 34px; background: var(--white); }
  .brand-front .brand-name {
    font-size: 54px; font-weight: 700; letter-spacing: 3px; text-transform: uppercase;
  }
  .slogan-row {
    position: absolute; left: 0; right: 0; bottom: 70px;
    display: flex; align-items: center; gap: 18px; padding: 0 0;
  }
  .slogan-row .rule { flex: 1; height: 1.5px; background: rgba(255,255,255,0.85); }
  .slogan { font-size: 19px; letter-spacing: 0.5px; white-space: nowrap; }

  /* Back */
  .card-back { background: var(--white); }
  .brand-back {
    position: absolute; top: 56px; right: 56px;
    display: flex; align-items: center; gap: 10px;
  }
  .brand-back .brand-mark { width: 20px; height: 20px; background: var(--blue); }
  .brand-back .brand-name {
    font-size: 28px; font-weight: 700; letter-spacing: 2px; text-transform: uppercase; color: var(--blue);
  }
  .services {
    position: absolute; top: 150px; right: 56px; list-style: none;
    color: var(--blue); font-size: 18px; text-align: right;
  }
  .services li { display: flex; align-items: center; justify-content: flex-end; gap: 12px; margin-bottom: 8px; }
  .services li::after { content: ""; width: 16px; height: 16px; background: var(--green); }
  .person { position: absolute; left: 56px; bottom: 60px; }
  .person-name { font-size: 30px; font-weight: 700; }
  .person-name .first { color: var(--blue); }
  .person-name .last { color: var(--green); }
  .credentials { font-size: 18px; color: var(--ink); margin: 2px 0 18px; }
  .contacts { list-style: none; font-size: 18px; color: var(--ink); }
  .contacts li { display: flex; align-items: center; gap: 14px; margin-bottom: 6px; }
  .icon { width: 26px; height: 26px; background: var(--blue); display: flex; align-items: center; justify-content: center; }
  .icon svg { width: 16px; height: 16px; }
</style>
</head>
<body>
  <section class="card card-front">
    <div class="brand-front">
      <span class="brand-mark"></span>
      <span class="brand-name">Varden Therapy</span>
    </div>
    <div class="slogan-row">
      <span class="rule"></span>
      <span class="slogan">Mobile Physiotherapy - Your Road To Recovery</span>
      <span class="rule"></span>
    </div>
  </section>

  <section class="card card-back">
    <div class="brand-back">
      <span class="brand-mark"></span>
      <span class="brand-name">Varden Therapy</span>
    </div>
    <ul class="services">
      <li>IMS</li>
      <li>Acupuncture</li>
      <li>Physiotherapy</li>
    </ul>
    <div class="person">
      <div class="person-name"><span class="first">Luke</span> <span class="last">Varden</span></div>
      <div class="credentials">BSc(kin), MPT, CAFCI, IMS</div>
      <ul class="contacts">
        <li><span class="icon"><svg viewBox="0 0 16 16"><path d="M4 1.5l2.5 3-1.5 1.5c.8 1.8 2.2 3.2 4 4l1.5-1.5 3 2.5-1.5 2.5C7 13.5 2.5 9 1.5 3z" fill="#fff"/></svg></span>867-555-0142</li>
        <li><span class="icon"><svg viewBox="0 0 16 16"><rect x="1.5" y="3.5" width="13" height="9" fill="none" stroke="#fff" stroke-width="1.4"/><path d="M1.5 3.5l6.5 5 6.5-5" fill="none" stroke="#fff" stroke-width="1.4"/></svg></span>VardenTherapy@postnest.ca</li>
        <li><span class="icon"><svg viewBox="0 0 16 16" fill="none" stroke="#fff" stroke-width="1.2"><circle cx="8" cy="8" r="6.3"/><ellipse cx="8" cy="8" rx="2.8" ry="6.3"/><path d="M1.7 8h12.6M2.8 4.8h10.4M2.8 11.2h10.4"/></svg></span>www.VardenTherapy.ca</li>
      </ul>
    </div>
  </section>
</body>
</html>
```